Plotvista Caribbean

We need a vibrant, user friendly and exciting website for our land search company called "plotVista" This application will help individuals locate and or list lots for sale within the Caribbean. We will offer a small cash back incentive to buyers that purchase land from our site, and we will charge a 1%-2% success fee to our sellers once a successful transaction is made. We would like to become a match making site, matching buyers and sellers on our platform. We will also include a service directory and marketing advertisement spot for other service providers for a fee. We would like to see a webdesign incorporating Caribbean colors (blue, green and yellow) with very modern clean lines, very picturesque and easy to use.

Industry/Entity Type

Real Estate

Coding

Coded - Design and coding required

Number of Pages Required

5+ page

Font styles to use
Sans Serif

Colors
ffffff
85acd3
b768aa
dbdbdb

Requirements
Nice to have
• Scenic photos of the ocean and beautiful landscape

```html
<!DOCTYPE html>
<html lang="en">
<head>
<meta charset="utf-8">
<title>plotVista – Caribbean Land Search</title>
<link rel="stylesheet" href="https://fonts.googleapis.com/css2?family=Roboto:wght@400;500;700&family=Open+Sans:wght@400;600;700&display=swap">
<style>
:root{
  --purple:#b768aa;
  --blue:#85acd3;
  --grey:#dbdbdb;
  --white:#ffffff;
  --ink:#222222;
  --muted:#555555;
  --footer:#4f4f4f;
}
*{box-sizing:border-box;margin:0;padding:0}
html,body{width:1200px;height:2875px;overflow:hidden}
body{position:relative;background:var(--white);font-family:'Open Sans',sans-serif;color:var(--ink)}
.abs{position:absolute}

/* header */
.site-header{left:0;top:0;width:1200px;height:100px;background:var(--white)}
.brand{left:100px;top:30px;font-family:'Roboto',sans-serif;font-weight:700;font-size:30px;color:var(--blue)}
.main-nav{right:100px;top:34px;display:flex;gap:10px}
.main-nav a{font-family:'Roboto',sans-serif;font-size:14px;font-weight:500;color:#333;text-decoration:none;padding:10px 18px;text-transform:uppercase}
.main-nav a.active{background:var(--purple);color:var(--white)}

/* hero */
.hero{left:0;top:100px;width:1200px;height:523px;background:linear-gradient(180deg,#3a2a3c 0%,#8a4a3a 22%,#e08a45 33%,#6b4a55 45%,#4a5a6a 62%,#9aa6ae 75%,#5a4238 88%,#3a2c26 100%)}
.hero-title{left:0;top:112px;width:1200px;text-align:center;font-family:'Roboto',sans-serif;font-weight:700;font-size:52px;color:var(--white)}
.hero-sub{left:0;top:207px;width:1200px;text-align:center;font-weight:600;font-size:20px;color:var(--white)}
.btn-outline-light{border:2px solid var(--white);color:var(--white);font-size:15px;text-transform:uppercase;display:flex;align-items:center;justify-content:center}
.hero-btn{left:538px;top:278px;width:124px;height:48px}
.slide-arrow{top:250px;width:30px;height:30px}

.promo{left:98px;top:552px;width:1002px;height:184px;background:var(--purple);box-shadow:0 30px 30px -22px rgba(0,0,0,.3)}
.promo-icon{left:66px;top:40px}
.promo-text{left:228px;top:40px;width:720px;font-family:'Roboto',sans-serif;font-size:20px;line-height:34px;color:var(--white)}

/* sections */
.section-title{left:0;width:1200px;text-align:center;font-family:'Roboto',sans-serif;font-size:28px;color:var(--purple)}
.section-intro{left:160px;width:880px;text-align:center;font-size:13px;line-height:22px;color:var(--muted)}

.feature{width:330px;text-align:center}
.feature-photo{margin:0 auto;width:242px;height:180px;border:1px solid #c8c8c8;padding:4px;background:var(--white)}
.feature-photo div{width:100%;height:100%}
.feature-name{margin-top:32px;font-family:'Roboto',sans-serif;font-size:17px;font-weight:500;color:var(--ink)}
.feature-name.hl{color:var(--purple)}
.feature-text{margin:14px auto 0;width:290px;font-size:13px;line-height:24px;color:var(--muted)}
.btn-dark{margin:20px auto 0;width:114px;height:42px;border:2px solid #333;border-radius:3px;font-family:'Roboto',sans-serif;font-size:13px;display:flex;align-items:center;justify-content:center;text-transform:uppercase;color:#222}
.btn-dark.fill{background:var(--purple);border-color:var(--purple);color:var(--white)}

.band{left:0;top:1436px;width:1200px;height:475px;background:var(--purple)}
.offer{top:84px;width:487px;height:311px;border:3px solid var(--white)}
.offer-title{left:182px;top:155px;font-family:'Open Sans',sans-serif;font-weight:700;font-size:24px;color:var(--white)}
.offer-sub{left:182px;top:190px;font-size:16px;font-weight:600;color:var(--white);letter-spacing:.5px}
.offer-btn{left:182px;top:235px;width:136px;height:38px;border-radius:20px;font-size:14px}

.post{top:2157px;width:485px;height:196px}
.post-photo{left:0;top:0;width:242px;height:196px}
.post-title{left:264px;top:2px;font-family:'Roboto',sans-serif;font-size:16px;font-weight:500;color:var(--ink)}
.post-text{left:264px;top:36px;width:220px;font-size:11.5px;line-height:22px;color:var(--muted);text-align:justify}
.btn-small{left:264px;top:160px;width:104px;height:36px;background:var(--purple);color:var(--white);font-family:'Roboto',sans-serif;font-size:13px;display:flex;align-items:center;justify-content:center}

/* footer */
.site-footer{left:0;top:2440px;width:1200px;height:435px;background:var(--footer);color:var(--white)}
.footer-brand{left:115px;top:152px;font-family:'Roboto',sans-serif;font-weight:700;font-size:28px}
.social{left:100px;top:212px;display:flex;gap:6px}
.social span{width:34px;height:34px;border:2px solid var(--white);border-radius:50%}
.f-head{font-family:'Roboto',sans-serif;font-size:18px;font-weight:500;text-transform:uppercase}
.f-head::after{content:"";display:block;width:100px;height:2px;background:var(--white);margin-top:12px}
.contact-item{display:flex;gap:16px;margin-top:22px}
.contact-item .ico{width:40px;height:40px;border:2px solid var(--white);border-radius:50%;flex:none;display:flex;align-items:center;justify-content:center}
.contact-item b{display:block;font-size:14px;font-weight:700;margin-bottom:4px}
.contact-item p{font-size:12.5px;line-height:20px}
.quick li{list-style:none;font-size:13.5px;margin-top:12px;display:flex;align-items:center;gap:10px}
.quick li::before{content:"";width:12px;height:12px;border-radius:50%;background:var(--white)}
.field{border:1px solid var(--white);border-radius:3px;font-size:11px;padding:9px 10px}
.send-btn{background:var(--white);color:var(--purple);font-size:12.5px;display:flex;align-items:center;justify-content:center;border-radius:2px}
.footer-rule{left:100px;top:2797px;width:1000px;height:1px;background:#8a8a8a}
.copyright{left:0;top:2822px;width:1200px;text-align:center;font-size:13px;color:var(--white)}
</style>
</head>
<body>

<header class="abs site-header">
  <div class="abs brand">plotVista</div>
  <nav class="abs main-nav">
    <a class="active">Home</a><a>About Us</a><a>Property</a><a>Blog</a><a>Gallery</a><a>Contact Us</a>
  </nav>
</header>

<section class="abs hero" role="img" aria-label="Sunset over the ocean with waves washing onto a sandy beach">
  <h1 class="abs hero-title">WELCOME TO PLOTVISTA</h1>
  <p class="abs hero-sub">We help individuals locate and or list lots for sale within the Caribbean.</p>
  <div class="abs btn-outline-light hero-btn">Read More</div>
  <svg class="abs slide-arrow" style="left:34px" viewBox="0 0 30 30"><circle cx="15" cy="15" r="14" fill="rgba(0,0,0,.25)"/><path d="M17 9l-6 6 6 6" stroke="#fff" stroke-width="2" fill="none"/></svg>
  <svg class="abs slide-arrow" style="right:34px" viewBox="0 0 30 30"><circle cx="15" cy="15" r="14" fill="rgba(0,0,0,.25)"/><path d="M13 9l6 6-6 6" stroke="#fff" stroke-width="2" fill="none"/></svg>
</section>
<svg class="abs" style="left:0;top:590px" width="1200" height="40" viewBox="0 0 1200 40">
  <path d="M0 30 Q60 12 120 8 L120 40 L0 40Z" fill="var(--purple)"/>
  <path d="M1200 30 Q1140 12 1080 8 L1080 40 L1200 40Z" fill="var(--purple)"/>
  <path d="M0 33 Q60 16 120 12 L1080 12 Q1140 16 1200 33 L1200 40 L0 40Z" fill="#fff"/>
</svg>

<section class="abs promo">
  <svg class="abs promo-icon" width="100" height="100" viewBox="0 0 100 100">
    <circle cx="50" cy="50" r="44" fill="none" stroke="#fff" stroke-width="6" stroke-dasharray="12 4"/>
    <circle cx="50" cy="50" r="32" fill="none" stroke="#fff" stroke-width="5"/>
    <path d="M36 64 L64 36" stroke="#fff" stroke-width="5" stroke-linecap="round"/>
    <circle cx="38" cy="39" r="6" fill="#fff"/><circle cx="62" cy="61" r="6" fill="#fff"/>
  </svg>
  <p class="abs promo-text">We will offer a small cash back incentive to buyers that purchase land from our site, and we will charge a 1%-2% success fee to our sellers once a successful transaction is made.</p>
</section>

<h2 class="abs section-title" style="top:824px">Matching Buyers And Sellers</h2>
<p class="abs section-intro" style="top:878px">We will offer a small cash back incentive to buyers that purchase land from our site, and we will charge a 1%-2% success fee to our sellers once a successful transaction is made.</p>

<article class="abs feature" style="left:75px;top:976px">
  <div class="feature-photo"><div role="img" aria-label="Golden sunset behind palm trees over an infinity pool" style="background:linear-gradient(180deg,#f5c24a,#e88a2a 45%,#2a7ea8 70%,#1ab0c8)"></div></div>
  <h3 class="feature-name">Accusantium Doloremque</h3>
  <p class="feature-text">Nemo enim ipsam voluptatem quia voluptas sit aspernatur aut odit aut fugit, sed quia con sequuntur magni dolores.</p>
  <div class="btn-dark">Read More</div>
</article>
<article class="abs feature" style="left:435px;top:976px">
  <div class="feature-photo"><div role="img" aria-label="Aerial view of turquoise water along a white sand beach" style="background:linear-gradient(135deg,#2a6a4a 0%,#e8e4d8 30%,#3ac0cc 55%,#1a8aa8 100%)"></div></div>
  <h3 class="feature-name hl">Nemo enim ipsam voluptatem</h3>
  <p class="feature-text">Nemo enim ipsam voluptatem quia voluptas sit aspernatur aut odit aut fugit, sed quia con sequuntur magni dolores.</p>
  <div class="btn-dark fill">Read More</div>
</article>
<article class="abs feature" style="left:793px;top:976px">
  <div class="feature-photo"><div role="img" aria-label="Tropical beach with palm trees and a green hill" style="background:linear-gradient(180deg,#7ac8ec 0%,#4a8a4a 45%,#e6e0cc 70%,#5ac0d8 100%)"></div></div>
  <h3 class="feature-name">Ratione voluptatem</h3>
  <p class="feature-text">Nemo enim ipsam voluptatem quia voluptas sit aspernatur aut odit aut fugit, sed quia con sequuntur magni dolores.</p>
  <div class="btn-dark">Read More</div>
</article>

<section class="abs band">
  <div class="abs offer" style="left:98px" role="img" aria-label="Leaning palm trees over a white beach and calm blue sea" >
    <div class="abs" style="inset:0;background:linear-gradient(180deg,#1a4a9a 0%,#3a7ac8 40%,#2aa8c0 65%,#e8e4dc 100%)"></div>
    <div class="abs offer-title">FULL PROPERTY</div>
    <div class="abs offer-sub">LANDSCAPE DESIGN</div>
    <div class="abs btn-outline-light offer-btn">Get Started</div>
  </div>
  <div class="abs offer" style="left:613px" role="img" aria-label="Palm-lined shore with a small boat under a cloudy blue sky">
    <div class="abs" style="inset:0;background:linear-gradient(180deg,#2a62b8 0%,#b8cce8 30%,#3a6a3a 60%,#2aa8b8 80%,#d8d4c4 100%)"></div>
    <div class="abs offer-title" style="left:195px">INCENTIVE TO BUYERS</div>
    <div class="abs offer-sub" style="left:195px">LANDSCAPE INSPIRATION</div>
    <div class="abs btn-outline-light offer-btn" style="left:195px">Get Started</div>
  </div>
</section>

<h2 class="abs section-title" style="top:1994px">Our Blog Posts</h2>
<p class="abs section-intro" style="top:2048px">We will offer a small cash back incentive to buyers that purchase land from our site, and we will charge a 1%-2% success fee to our sellers once a successful transaction is made.</p>

<article class="abs post" style="left:98px">
  <div class="abs post-photo" role="img" aria-label="Beach umbrella and two lounge chairs on the sand" style="background:linear-gradient(180deg,#4a9ad8 0%,#8ac8e8 40%,#2ab0c0 60%,#e4d6b8 80%,#cdb892 100%)"></div>
  <h3 class="abs post-title">NEQUE PORRO QUISQUAM</h3>
  <p class="abs post-text">Solar panels are a great way to tap into the free power from our Australian sun! With more usable sunlight than any other country in the world we really do think getting solar is a no brainer!</p>
  <div class="abs btn-small">CLICK HERE</div>
</article>
<article class="abs post" style="left:615px">
  <div class="abs post-photo" role="img" aria-label="Palm trees and lights along a beach at dusk" style="background:linear-gradient(180deg,#8aa8c8 0%,#5a6a58 40%,#3a4a3a 60%,#b89a7a 85%,#d8c0a0 100%)"></div>
  <h3 class="abs post-title">NEMO ENIM IPSAM</h3>
  <p class="abs post-text">Solar panels are a great way to tap into the free power from our Australian sun! With more usable sunlight than any other country in the world we really do think getting solar is a no brainer!</p>
  <div class="abs btn-small">CLICK HERE</div>
</article>

<footer class="abs site-footer">
  <div class="abs footer-brand">plotVista</div>
  <div class="abs social"><span></span><span></span><span></span><span></span></div>

  <div class="abs" style="left:343px;top:76px;width:240px">
    <h4 class="f-head">Contact Us</h4>
    <div class="contact-item">
      <div class="ico"><svg width="16" height="20" viewBox="0 0 16 20"><path d="M8 1a6 6 0 0 0-6 6c0 5 6 12 6 12s6-7 6-12a6 6 0 0 0-6-6z" fill="#fff"/><circle cx="8" cy="7" r="2.3" fill="var(--footer)"/></svg></div>
      <div><b>ADDRESS,</b><p>45 Harbour Lane, Bridgetown<br>210, BB</p></div>
    </div>
    <div class="contact-item">
      <div class="ico"><svg width="12" height="18" viewBox="0 0 12 18"><rect x="1" y="1" width="10" height="16" rx="2" fill="none" stroke="#fff" stroke-width="2"/><circle cx="6" cy="14" r="1" fill="#fff"/></svg></div>
      <div><b>PHONE:</b><p>180 555 0148</p></div>
    </div>
    <div class="contact-item">
      <div class="ico"><svg width="18" height="14" viewBox="0 0 18 14"><rect x="1" y="1" width="16" height="12" fill="#fff"/><path d="M1 1l8 7 8-7" stroke="var(--footer)" stroke-width="1.5" fill="none"/></svg></div>
      <div><b>Mail:</b><p>info@plotVista.com</p></div>
    </div>
  </div>

  <div class="abs" style="left:629px;top:76px;width:180px">
    <h4 class="f-head">Quick Links</h4>
    <ul class="quick" style="margin-top:12px">
      <li>Home</li><li>About Us</li><li>Property</li><li>Blog</li><li>Gallery</li><li>Contact us</li>
    </ul>
  </div>

  <div class="abs" style="left:847px;top:76px;width:253px">
    <h4 class="f-head">Contact Form</h4>
    <div class="abs field" style="left:0;top:54px;width:122px;height:36px">Name</div>
    <div class="abs field" style="left:131px;top:54px;width:122px;height:36px">Phone</div>
    <div class="abs field" style="left:0;top:98px;width:253px;height:66px">Address</div>
    <div class="abs send-btn" style="left:0;top:178px;width:120px;height:38px">SEND MESSAGE</div>
  </div>
</footer>
<div class="abs footer-rule"></div>
<p class="abs copyright">Copyright © 2017 plotVista. All Right Reserved</p>

</body>
</html>
```